Call Center In Need of Website Design

We are a call center that provides inbound and outbound calling & marketing services for eCommerce store. We would like to see a fun, creative, playful design that is simple.

Here are some sample design sites we like;
- https://www.velmoreline.com/
- https://pindrask.io/
- https://www.glimbertic.com/live-chat-software/
- https://www.zavrolin.com/

Here are some competitor sites;
- https://www.ostrevaglinks.com/
- https://www.helpkestrel.com/

I have attached website content for your use.

Target Market(s)

eCommerce

Coding

Coded - Design and coding required

Number of Pages Required

5+ page

Font styles to use
Sans Serif

Colors

Designer to choose colors to be used in the design.

Requirements
Must have
• Must have designs for the following 5 separate pages;
• 1. Home (landing)
• - This will be were the design style really needs to show.
• - Just needs to touch on key services
• - CTA
• 2. About Us
• - Basic page for about me paragraph
• 3. Services
• - List of services with icons
• - Click on service type to expand details or hover over service icon to view popup bubble with details about that service
• 4. Pricing
• - Option to bundle 1(one) digital service plan and 1(one) call center service plan
• - Bundling adds 10% monthly discount to over all price
• - Customer does NOT have to bundle
• - FAQ
• 5. Contact Us
• - Include a capture form (name, company name, email, phone, message)
• - Contact info
• - Business hours
• When customer purchases their desired plan, then they are taken to a page where they must schedule a call with an account rep.
Nice to have
• home page animations
Should not have
• All information on Home/Landing page.

```html
<!DOCTYPE html>
<html lang="en">
<head>
<meta charset="utf-8">
<title>Loftwave – Pricing</title>
<link href="https://fonts.googleapis.com/css2?family=Anton&family=Lato:wght@400;700;900&family=Montserrat:wght@400;500;600&display=swap" rel="stylesheet">
<style>
:root{
  --space:#383a8a;
  --navy:#2f3183;
  --mint:#6cc8ae;
  --mint-light:#7fd9c1;
  --white:#ffffff;
  --ink:#333333;
  --grey-card:#7f7f7f;
  --grey-dark:#6d6d6d;
  --blue-card:#4a90d6;
  --blue-dark:#2f6db6;
  --teal-card:#3aaa98;
  --orange-card:#f8682f;
  --orange-dark:#ef5720;
  --faq-bg:#f4f4f4;
  --muted:#777777;
}
*{box-sizing:border-box;margin:0;padding:0}
html,body{width:1200px;height:2605px;overflow:hidden;background:var(--white)}
body{position:relative;font-family:"Lato",sans-serif;color:var(--ink)}
.abs{position:absolute}

/* hero */
.hero{left:0;top:0;width:1200px;height:634px;background:var(--space);overflow:hidden}
.cloud-band{left:0;top:370px;width:1200px;height:264px;background:linear-gradient(180deg,#62bfa7 0%,var(--mint) 40px,var(--mint) 100%)}
.brand{left:161px;top:40px;display:flex;align-items:center;gap:16px;color:var(--white);font-family:"Montserrat",sans-serif;font-weight:500;font-size:36px;letter-spacing:5px}
.brand-dot{width:34px;height:34px;border:4px solid var(--mint);border-radius:50%}
.nav{left:563px;top:42px;display:flex;gap:35px;font-family:"Montserrat",sans-serif;font-size:11px;font-weight:600;color:var(--white);letter-spacing:.3px}
.nav .active{border-bottom:2px solid var(--white);padding-bottom:4px}
.hero-title{left:160px;top:152px;font-family:"Anton",sans-serif;font-size:60px;line-height:68px;color:var(--white);letter-spacing:1px}
.hero-sub{left:160px;top:301px;font-family:"Montserrat",sans-serif;font-size:17px;letter-spacing:3.5px;color:var(--white)}
.art-astronaut{left:790px;top:100px;width:410px;height:285px;background:radial-gradient(ellipse at 55% 45%,#e9ecf7 0%,#9aa0d4 45%,rgba(56,58,138,0) 75%)}
.art-rocket{left:52px;top:105px;width:44px;height:270px;background:linear-gradient(180deg,var(--mint) 0%,rgba(108,200,174,.4) 100%);border-radius:22px 22px 4px 4px}
.art-lander{left:0;top:442px;width:158px;height:192px;background:radial-gradient(ellipse at 40% 60%,#e8f7f2 0%,rgba(108,200,174,0) 70%)}
.page-label{left:276px;top:502px;display:flex;align-items:center;gap:10px;font-family:"Anton",sans-serif;font-size:26px;color:var(--white);letter-spacing:1px}
.page-label i{display:block;width:34px;height:10px;border-top:2px solid var(--white);border-bottom:2px solid var(--white)}

/* plans */
.plan{width:214px;border:4px solid;border-radius:4px;overflow:hidden}
.plan-head{height:42px;display:flex;align-items:center;justify-content:center;font-weight:900;font-size:14px;color:var(--white);letter-spacing:.3px;white-space:nowrap}
.plan-price{height:96px;display:flex;flex-direction:column;align-items:center;justify-content:center;color:var(--white)}
.plan-price .amt{display:flex;align-items:flex-end;gap:4px}
.plan-price b{font-size:30px;font-weight:700;line-height:1}
.plan-price sup{font-size:13px;align-self:flex-start;margin-top:2px}
.plan-price small{font-size:10px;font-weight:700;margin-bottom:4px}
.plan-price em{font-style:normal;font-size:11px;font-weight:700;margin-top:2px}
.plan-body{background:var(--white);margin:0 6px 8px;border-radius:4px;padding:18px 4px 20px 10px}
.features{list-style:none;font-size:11px;line-height:22.5px;color:var(--ink);white-space:nowrap}
.features li{padding-left:12px;position:relative}
.features li::before{content:"";position:absolute;left:0;top:8px;width:6px;height:6px;border:1px solid var(--ink);border-radius:50%}
.features li.note::before{display:none}
.signup{display:flex;align-items:center;justify-content:center;gap:8px;width:132px;height:38px;margin:28px auto 0;border-radius:3px;color:var(--white);font-weight:700;font-size:13px}
.signup svg{width:14px;height:14px}
.p-grey{left:161px;top:709px;border-color:var(--grey-card);background:var(--grey-card)}
.p-grey .plan-head,.p-grey .signup{background:var(--grey-dark)}
.p-blue{left:382px;top:709px;border-color:var(--blue-card);background:var(--blue-card)}
.p-blue .plan-head,.p-blue .signup{background:var(--blue-dark)}
.p-teal{left:603px;top:709px;border-color:var(--mint);background:var(--mint)}
.p-teal .plan-head,.p-teal .signup{background:var(--teal-card)}
.p-orange{left:823px;top:709px;border-color:var(--orange-card);background:var(--orange-card)}
.p-orange .plan-head,.p-orange .signup{background:var(--orange-dark)}

/* faq */
.section-mark{width:34px;height:8px;border-top:2px solid var(--navy);border-bottom:2px solid var(--navy)}
.faq-title{left:0;width:1200px;top:1466px;text-align:center;font-family:"Anton",sans-serif;font-size:30px;color:var(--navy);letter-spacing:.5px}
.faq-item{width:424px;height:37px;background:var(--faq-bg);border:1px solid #e6e6e6;display:flex;align-items:center;justify-content:space-between;padding:0 14px;font-size:11.5px;font-weight:700;color:var(--ink)}
.faq-item .sign{font-size:20px;font-weight:900}
.faq-open{left:161px;top:1528px;width:424px;height:134px;background:var(--mint)}
.faq-open .q{height:37px;display:flex;align-items:center;justify-content:space-between;padding:0 14px;font-size:11.5px;font-weight:700;color:var(--white);border-bottom:1px solid rgba(255,255,255,.5)}
.faq-open p{padding:12px 14px;font-size:11.5px;line-height:16px;color:var(--white)}

/* cta */
.cta-title{left:0;width:1200px;top:1905px;text-align:center;font-family:"Anton",sans-serif;font-size:44px;line-height:54px;color:var(--navy);letter-spacing:1px}
.cta-btn{left:519px;top:2039px;width:160px;height:45px;border-radius:23px;background:var(--mint);color:var(--white);font-family:"Montserrat",sans-serif;font-weight:600;font-size:12px;display:flex;align-items:center;justify-content:center}
.art-rocket-right{left:990px;top:1900px;width:130px;height:263px;background:radial-gradient(ellipse at 50% 40%,var(--mint) 0%,rgba(108,200,174,.5) 45%,rgba(255,255,255,0) 72%)}

/* contact */
.contact-band{left:0;top:2163px;width:1200px;height:344px;background:var(--mint)}
.contact-card{left:188px;top:2220px;width:274px;height:235px;background:var(--mint-light);padding:30px 22px;color:var(--white);box-shadow:0 4px 14px rgba(0,0,0,.08)}
.contact-card h3{font-family:"Montserrat",sans-serif;font-size:15px;font-weight:600;padding-bottom:14px;border-bottom:1px solid rgba(255,255,255,.6)}
.contact-card ul{list-style:none;margin-top:24px;font-size:11.5px;line-height:15px}
.contact-card li{display:flex;gap:10px;margin-bottom:13px}
.contact-card svg{width:12px;height:12px;flex:none;margin-top:2px}
.form-title{left:488px;top:2220px;font-family:"Montserrat",sans-serif;font-size:27px;font-weight:500;color:var(--white)}
.field{width:254px;height:38px;background:var(--mint-light);padding:0 14px;display:flex;align-items:center;font-size:11px;color:var(--white)}
.submit{left:488px;top:2406px;width:104px;height:38px;border:2px solid var(--white);border-radius:4px;display:flex;align-items:center;justify-content:center;color:var(--white);font-weight:700;font-size:11.5px}

/* footer */
.copyright{left:161px;top:2537px;font-size:11px;line-height:20px;color:var(--muted)}
.footer-nav{left:412px;top:2548px;display:flex;gap:28px;font-size:12px;color:var(--muted)}
.footer-nav .active{color:var(--mint)}
.social{left:920px;top:2545px;display:flex;gap:7px}
.social span{width:24px;height:24px;border-radius:3px;display:block}
</style>
</head>
<body>

<header class="hero abs">
  <div class="art-astronaut abs" role="img" aria-label="Illustration of an astronaut floating among sparkling stars"></div>
  <div class="art-rocket abs" role="img" aria-label="Illustration of a small rocket launching with a vapour trail"></div>
  <div class="cloud-band abs" role="img" aria-label="Illustration of soft mint clouds along the bottom of the hero"></div>
  <div class="art-lander abs" role="img" aria-label="Illustration of an astronaut planting a flag on a small hill"></div>

  <div class="brand abs"><span class="brand-dot"></span>LOFTWAVE</div>
  <nav class="nav abs">
    <span class="active">HOME</span><span>ABOUT US</span><span>SERVICES</span><span>PRICING</span><span>CONTACT US</span><span>ACCOUNT</span>
  </nav>
  <h1 class="hero-title abs">Loftwave Is An<br>Omnichannel</h1>
  <p class="hero-sub abs">Provider For Customer Care</p>
  <div class="page-label abs"><i></i>PRICING</div>
</header>

<section class="plan p-grey abs">
  <div class="plan-head">DIGITAL STANDARD</div>
  <div class="plan-price"><div class="amt"><sup>$</sup><b>199</b><small>PER MONTH</small></div></div>
  <div class="plan-body">
    <ul class="features">
      <li>Unlimited Email Support</li><li>Limited Live Chat Support</li><li>Product Research (5 per month)</li>
      <li>Product Listing (5 per month)</li><li>Price Monitoring</li><li class="note">(10 products per month)</li>
      <li>Product Photo &amp; Video Editing</li><li class="note">(5 photos &amp; 1, 10 second video)</li>
    </ul>
    <div class="signup">Sign Up <svg viewBox="0 0 14 14" fill="none" stroke="#fff" stroke-width="2"><path d="M1 7h8M6 4l3 3-3 3M9 1h4v12H9"/></svg></div>
  </div>
</section>

<section class="plan p-blue abs">
  <div class="plan-head">CALL CENTER STANDARD</div>
  <div class="plan-price"><div class="amt"><sup>$</sup><b>39</b><small>PER MONTH</small></div><em>(7 DAY FREE TRIAL)</em></div>
  <div class="plan-body">
    <ul class="features">
      <li>Pay Per Minute</li><li>$1.10 Per Minute</li><li>Live Personalized Receptionist</li><li>Text &amp; Email Delivery</li>
      <li>Includes Nationwide 800</li><li>Answering service</li><li>Welcome Calls</li><li>Follow-Up Service</li>
      <li>Customer Upselling</li><li>Over-The-Phone Order Taking</li><li>Order Return Processing</li><li>Feedback/Survey Calls</li>
      <li>Message Delivering Service</li><li>ROI Diagnostics &amp; Reporting</li><li>Scalable Call Center Pricing</li>
      <li>Customizable For Any Industry</li><li>100% US-Based Agents</li>
    </ul>
    <div class="signup">Sign Up <svg viewBox="0 0 14 14" fill="none" stroke="#fff" stroke-width="2"><path d="M1 7h8M6 4l3 3-3 3M9 1h4v12H9"/></svg></div>
  </div>
</section>

<section class="plan p-teal abs">
  <div class="plan-head">DIGITAL BUSINESS</div>
  <div class="plan-price"><div class="amt"><sup>$</sup><b>199</b><small>PER MONTH</small></div></div>
  <div class="plan-body">
    <ul class="features">
      <li>Unlimited Email Support</li><li>Unlimited Live Chat Support</li><li>Product Research (20 per month)</li>
      <li>Product Listing (20 per month)</li><li>Price Monitoring (50 permonth)</li><li>Product Photo &amp; Video Editing</li>
      <li class="note">(20 photos &amp; 5, 10 second videos)</li>
    </ul>
    <div class="signup">Sign Up <svg viewBox="0 0 14 14" fill="none" stroke="#fff" stroke-width="2"><path d="M1 7h8M6 4l3 3-3 3M9 1h4v12H9"/></svg></div>
  </div>
</section>

<section class="plan p-orange abs">
  <div class="plan-head">CALL CENTER BUSINESS</div>
  <div class="plan-price"><div class="amt"><sup>$</sup><b>249</b><small>PER MONTH</small></div><em>(7 DAY FREE TRIAL)</em></div>
  <div class="plan-body">
    <ul class="features">
      <li>225 Minutes</li><li>$1.05 Per Minute</li><li>Live Personalized Receptionist</li><li>Text &amp; Email Delivery</li>
      <li>Includes Nationwide 800 Number</li><li>Answering service</li><li>Welcome Calls</li><li>Follow-Up Service</li>
      <li>Customer Upselling</li><li>Over-The-Phone Order Taking</li><li>Order Return Processing</li><li>Feedback/Survey Calls</li>
      <li>Message Delivering Service</li><li>ROI Diagnostics &amp; Reporting</li><li>Scalable Call Center Pricing</li>
      <li>Customizable For Any Industry</li><li>100% US-Based Agents</li>
    </ul>
    <div class="signup">Sign Up <svg viewBox="0 0 14 14" fill="none" stroke="#fff" stroke-width="2"><path d="M1 7h8M6 4l3 3-3 3M9 1h4v12H9"/></svg></div>
  </div>
</section>

<div class="section-mark abs" style="left:583px;top:1452px"></div>
<h2 class="faq-title abs">Frequently Asked Questions</h2>

<div class="faq-open abs">
  <div class="q">IS THE FREE TRIAL REALLY FREE? <span style="font-size:20px">−</span></div>
  <p>The free trial only relates to the "call center" service packages! There is no hidden fine print or fees to get started. We don't even require any payment info, signatures, or deposits. If you don't like us or our service, just simply walk away.</p>
</div>
<div class="faq-item abs" style="left:161px;top:1671px">Do you offer custom script writing? <span class="sign">+</span></div>
<div class="faq-item abs" style="left:161px;top:1716px">Why do you use time-based billing over standard billing? <span class="sign">+</span></div>
<div class="faq-item abs" style="left:161px;top:1761px">How long does it take to get started? <span class="sign">+</span></div>
<div class="faq-item abs" style="left:615px;top:1528px">Do I have to sign a contract? <span class="sign">+</span></div>
<div class="faq-item abs" style="left:615px;top:1574px">Do I have to purchase any hardware or equipment? <span class="sign">+</span></div>
<div class="faq-item abs" style="left:615px;top:1619px">I'm not sure how many minutes I'll need? <span class="sign">+</span></div>
<div class="faq-item abs" style="left:615px;top:1664px">Can I change my service plan? <span class="sign">+</span></div>

<h2 class="cta-title abs">READY TO TAKE YOUR BUSINESS<br>TO THE NEXT LEVEL</h2>
<div class="cta-btn abs">GET STARTED</div>
<div class="art-rocket-right abs" role="img" aria-label="Illustration of a glowing rocket lifting off from clouds"></div>

<section class="contact-band abs" role="img" aria-label="Faint illustration of an astronaut on the moon behind the contact area"></section>
<div class="contact-card abs">
  <h3>Contact Details</h3>
  <ul>
    <li><svg viewBox="0 0 12 12" fill="#fff"><path d="M2.5 0.5l2 2.5-1.2 1.5c.7 1.5 2 2.8 3.5 3.5L8.3 7l2.7 2-1 2.3C5 11 1 7 0.7 2z"/></svg>Phone: (800) 555-0147</li>
    <li><svg viewBox="0 0 12 12" fill="#fff"><path d="M0 2h12v8H0zM0 2l6 4 6-4" stroke="#7fd9c1" stroke-width="1"/></svg>hello@loftwave.inc</li>
    <li><svg viewBox="0 0 12 12" fill="#fff"><path d="M6 0a4 4 0 0 1 4 4c0 3-4 8-4 8S2 7 2 4a4 4 0 0 1 4-4z"/><circle cx="6" cy="4" r="1.5" fill="#7fd9c1"/></svg><span>Loftwave, Inc.<br>418 Corvell Ave. Fresno, CA 93721</span></li>
  </ul>
</div>
<h3 class="form-title abs">Request For Call Back</h3>
<div class="field abs" style="left:488px;top:2295px">Name</div>
<div class="field abs" style="left:759px;top:2295px">Email</div>
<div class="field abs" style="left:488px;top:2347px">Ph Num</div>
<div class="field abs" style="left:759px;top:2347px">Enquiry About</div>
<div class="submit abs">Submit Now</div>

<footer>
  <p class="copyright abs">Copyright © 2018<br>All rights reserved.</p>
  <nav class="footer-nav abs"><span class="active">Home</span><span>About Us</span><span>Service</span><span>Pricing</span><span>Contact Us</span><span>Account</span></nav>
  <div class="social abs">
    <span style="background:#2a9fd6"></span><span style="background:#3b5998"></span><span style="background:#4a78a8"></span><span style="background:#dd4b39"></span>
  </div>
</footer>

</body>
</html>
```